Ward Compass Business Card Design*

We need a business card design for our company Ward Compass. Our company is specialized in providing online consulting services regarding medical institutions, hospitals and doctors. We work with patients worldwide looking to choose between healthcare providers. We have a website you may use as a reference, where we list doctors and clinics worldwide. So we target Medical providers as well as patients worldwide.
Target Market(s)
Medical Providers and patients around the world
Industry/Entity Type
Medical
Contact Information for Business Card
Salwa Kettani
CEO
+90 612 348 2175
info@wardcompass.example
www.wardcompass.example
14 Annakhil 7 H.R.B. Rabat, Morocco
Requirements
Must have
- Company logo/name on one full side, personal info and smaller logo and company name on the other side.
Nice to have
- Smart and elegant design

```html
<!DOCTYPE html>
<html lang="en">
<head>
<meta charset="utf-8">
<title>Ward Compass Business Card</title>
<link rel="stylesheet" href="https://fonts.googleapis.com/css2?family=Montserrat:wght@400;600;700&family=Open+Sans:wght@400;600&display=swap">
<style>
  :root {
    --navy: #143664;
    --grey: #808082;
    --white: #ffffff;
    --ink: #2b2b2b;
    --backdrop: #dcdcda;
  }
  * { margin: 0; padding: 0; box-sizing: border-box; }
  html, body {
    width: 1200px; height: 801px; overflow: hidden;
    background: var(--backdrop);
  }
  .canvas {
    position: relative; width: 1200px; height: 801px;
  }
  .card {
    position: absolute; top: 252px;
    width: 520px; height: 297px;
    overflow: hidden;
    box-shadow: 0 6px 18px rgba(0,0,0,0.18);
  }
  .card--front { left: 50px; background: var(--white); }
  .card--back  { left: 630px; background: var(--navy); }

  .swoosh { position: absolute; inset: 0; width: 100%; height: 100%; }

  .brand {
    position: absolute; display: flex; align-items: center; gap: 10px;
    font-family: "Montserrat", sans-serif; font-weight: 600;
    letter-spacing: 0.06em; text-transform: uppercase;
  }
  .brand__dot { border-radius: 50%; flex: none; }

  .card--front .brand { left: 36px; top: 168px; font-size: 22px; color: var(--navy); }
  .card--front .brand__dot { width: 26px; height: 26px; background: var(--navy); }

  .person {
    position: absolute; left: 36px; top: 222px;
    font-family: "Open Sans", sans-serif; color: var(--ink);
  }
  .person__name {
    font-family: "Montserrat", sans-serif; font-weight: 700;
    font-size: 15px; color: var(--navy);
  }
  .person__role { font-size: 11px; margin-bottom: 6px; }
  .person__address { font-size: 11px; line-height: 1.35; }

  .contact {
    position: absolute; right: 26px; top: 150px;
    list-style: none;
    font-family: "Open Sans", sans-serif; font-size: 11px; color: var(--ink);
  }
  .contact__item { display: flex; align-items: center; gap: 8px; margin-bottom: 5px; }
  .contact__icon { width: 11px; height: 11px; flex: none; }

  .card--back .brand {
    left: 50%; top: 118px; transform: translateX(-50%);
    font-size: 34px; color: var(--white); white-space: nowrap; gap: 14px;
  }
  .card--back .brand__dot { width: 40px; height: 40px; background: var(--grey); }
  .back__url {
    position: absolute; left: 0; right: 0; bottom: 46px; text-align: center;
    font-family: "Open Sans", sans-serif; font-size: 13px;
    letter-spacing: 0.08em; color: var(--white);
  }
</style>
</head>
<body>
<main class="canvas">

  <section class="card card--front" aria-label="Business card, contact side">
    <svg class="swoosh" viewBox="0 0 520 297" preserveAspectRatio="none" aria-hidden="true">
      <path d="M0 0 H520 V36 Q250 52 0 150 Z" fill="var(--navy)"/>
      <path d="M0 156 Q250 60 520 44 V58 Q270 74 0 170 Z" fill="var(--grey)"/>
    </svg>

    <div class="brand"><span class="brand__dot"></span>Ward Compass</div>

    <div class="person">
      <p class="person__name">Salwa Kettani</p>
      <p class="person__role">CEO</p>
      <p class="person__address">14 Annakhil 7<br>H.R.B. Rabat, Morocco</p>
    </div>

    <ul class="contact">
      <li class="contact__item">
        <svg class="contact__icon" viewBox="0 0 12 12" aria-hidden="true"><path d="M2.5 1 L4.5 1 L5.2 3.6 L4 4.5 Q5 7 7.5 8 L8.4 6.8 L11 7.5 V9.5 Q11 11 9.5 11 Q1 10 1 2.5 Q1 1 2.5 1 Z" fill="var(--navy)"/></svg>
        +90 612 348 2175
      </li>
      <li class="contact__item">
        <svg class="contact__icon" viewBox="0 0 12 12" aria-hidden="true"><rect x="0.5" y="2" width="11" height="8" fill="var(--navy)"/><path d="M0.5 2 L6 6.5 L11.5 2" stroke="var(--white)" fill="none"/></svg>
        info@wardcompass.example
      </li>
      <li class="contact__item">
        <svg class="contact__icon" viewBox="0 0 12 12" aria-hidden="true"><circle cx="6" cy="6" r="5.5" fill="var(--navy)"/><path d="M0.5 6 H11.5 M6 0.5 V11.5 M2 3.5 H10 M2 8.5 H10" stroke="var(--white)" stroke-width="0.7"/></svg>
        www.wardcompass.example
      </li>
    </ul>
  </section>

  <section class="card card--back" aria-label="Business card, brand side">
    <div class="brand"><span class="brand__dot"></span>Ward Compass</div>
    <p class="back__url">www.wardcompass.example</p>
  </section>

</main>
</body>
</html>
```